Banner design for Brindley & Oakhurst Chamber of Commerce

We would like a design for banners that will hang in the towns of Brindley & Oakhurst located in southwestern Ontario, Canada. We have some specific things that need to be included on the banner.

The logo from our website must appear at the top of the banner using the logo and same colours. i.e. Brindley in white lettering, green background. See logo and colour specifics that have been provided in digital form.

There is one addition we would like in the logo. Below "Tour Brindley" and above the tag line "a great place to grow" we want to add "& Oakhurst" using one of the two fonts already being used in the logo.

At the bottom of the banner (against the green colour) we would like it to read: Chamber of Commerce on one line and below this the web address, www.tourbrindley.ca

The space on the banner in between the top and the bottom of the banner we would like to see images that include the following representations: 1. Wine/glasses of wine/grapes/vineyards (vineyards should reflect the Lake Erie North Shore wine region) 2. Industry (we have many large industries in our town) including Corvin Pipe, Dunmore Equipment, Voltaris, Pinecrest Fuel, possibly these could be represented by a single image representing industry. 3. Agriculture keep in mind that we are located in southwestern Ontario and we would like the image(s) to reflective of our agricultural area. We are also known for our greenhouse technology in our region and we grow tomatoes, corn, soybeans, cucumbers, peppers, asparagus and we also have orchards of apples, pears, and peaches. 4. Oakhurst harbour located on the north shore of Lake Erie in the village of Oakhurst. These are listed in order of importance, and so the size and frequency of the images should reflect this. The wineries located in Brindley and Oakhurst represent the most important tourism attraction in our towns.

These banners will be placed in both the towns of Brindley and Oakhurst along the main entrances and thoroughfares. These vertical banners will be seen as visitors enter our town(s). We want them to be colourful and beautiful/elegant; but easily recognizable and easily read by passing motorists.

See also http://explorebaymarkvale.com/ for ideas.

The dimensions for the banners are: 60" in height and 24" in width.

Please provide us with digital files that are print ready.

Thank you,
Cheers,
Melissa Toft
Director Brindley & Oakhurst Chamber of Commerce

Target Market(s)

Tourists, potential business investors

Industry/Entity Type

Chamber Of Commerce

Font styles to use
Other font styles liked:
• The font(s) used in our existing logo, file is provided

Requirements
Must have
• Must be designed to fit dimensions for banner. See project description for other must haves.
Nice to have
• See project description.
Should not have
• Should not have images that do not reflect our region of southwestern Ontario.

```html
<!DOCTYPE html>
<html lang="en">
<head>
<meta charset="utf-8">
<title>Tour Brindley – Street Banner</title>
<link rel="stylesheet" href="https://fonts.googleapis.com/css2?family=Arimo:wght@400;700&display=swap">
<style>
  :root {
    --green: #7ab940;
    --purple: #7a55a8;
    --blue: #1f9ad8;
    --frame: #4a4a4a;
    --white: #ffffff;
    --page: #ffffff;
    --ink: #1c1c1c;
  }
  * { box-sizing: border-box; margin: 0; padding: 0; }
  html, body {
    width: 1200px; height: 1000px; overflow: hidden;
    background: var(--page);
    font-family: "Arimo", Arial, sans-serif;
  }
  .banner {
    position: absolute; left: 414px; top: 38px;
    width: 372px; height: 926px;
    border: 3px solid var(--frame);
    background: var(--white);
    display: flex; flex-direction: column;
  }
  .banner-header {
    height: 137px; background: var(--green); color: var(--white);
    text-align: center; padding-top: 10px;
  }
  .brand-name {
    font-size: 46px; font-weight: 400; line-height: 52px; letter-spacing: 1px;
  }
  .brand-town {
    font-size: 21px; letter-spacing: 4px; line-height: 24px; margin-top: 2px;
  }
  .tagline {
    font-size: 21px; letter-spacing: 2.5px; line-height: 28px; color: var(--ink);
    margin-top: 4px;
  }
  .tile-grid {
    flex: 1;
    display: grid;
    grid-template-columns: 1fr 1fr;
    grid-template-rows: 132fr 135fr 135fr 148fr 139fr;
    gap: 3px;
    padding: 3px 0;
    background: var(--white);
  }
  .photo { width: 100%; height: 100%; }
  .photo-canola { background: linear-gradient(#6fa3dc 0%, #a8c8ea 45%, #e6d62a 55%, #c9b81e 100%); }
  .photo-vineyard { background: linear-gradient(#d9822e 0%, #b8a03c 45%, #58762a 100%); }
  .photo-lake { background: linear-gradient(#2f5a2a 0%, #48703a 50%, #5b7f8a 70%, #3c5d6a 100%); }
  .photo-pour { background: radial-gradient(circle at 60% 60%, #7a1020 0%, #a8323a 35%, #e8d2b4 75%); }
  .photo-orchard { background: linear-gradient(#5d8a3a 0%, #3e6a25 55%, #6a8a3a 100%); }
  .photo-industry { background: linear-gradient(#7a6a4e 0%, #2f4a7a 60%, #5a5048 100%); }
  .photo-hay { background: linear-gradient(#dfe6c8 0%, #c59a3c 30%, #b07a28 100%); }
  .feature-tile {
    color: var(--white);
    display: flex; flex-direction: column; align-items: center; justify-content: center;
    text-align: center; font-size: 17px; line-height: 19px;
  }
  .feature-tile svg { margin-bottom: 6px; }
  .tile-tourism { background: var(--green); }
  .tile-wine { background: var(--purple); }
  .tile-agri { background: var(--blue); font-size: 19px; line-height: 26px; }
  .banner-footer {
    height: 80px; background: var(--green); text-align: center;
  }
  .footer-title {
    color: var(--white); font-size: 25px; letter-spacing: 1.5px; padding-top: 16px;
  }
  .footer-web {
    color: var(--ink); font-size: 13px; letter-spacing: 3px; margin-top: 12px;
  }
</style>
</head>
<body>
  <main class="banner">
    <header class="banner-header">
      <div class="brand-name">Tour Brindley</div>
      <div class="brand-town">&amp; OAKHURST</div>
      <div class="tagline">a great place to grow</div>
    </header>

    <section class="tile-grid">
      <div class="photo photo-canola" role="img" aria-label="Red barn and silo behind a yellow canola field under blue sky"></div>
      <div class="photo photo-vineyard" role="img" aria-label="Wine bottle, glass and grapes before vineyard rows at sunset"></div>

      <div class="photo photo-lake" role="img" aria-label="Lakeside cottage among pine trees with a wooden dock"></div>
      <div class="feature-tile tile-tourism">
        <svg width="96" height="42" viewBox="0 0 96 42" aria-hidden="true">
          <path d="M6 30 L44 30 L38 38 L12 38 Z" fill="#fff"/>
          <path d="M24 4 L24 28 L8 28 Z" fill="#fff"/>
          <path d="M27 8 L27 28 L40 28 Z" fill="#fff"/>
          <circle cx="56" cy="30" r="7" fill="none" stroke="#fff" stroke-width="2"/>
          <circle cx="78" cy="30" r="7" fill="none" stroke="#fff" stroke-width="2"/>
          <path d="M56 30 L63 20 L74 20 L78 30 M63 20 L67 30 L74 20" fill="none" stroke="#fff" stroke-width="2"/>
          <rect x="84" y="22" width="10" height="12" fill="#fff"/>
        </svg>
        <span>Tourism, Nature<br>&amp; Shopping</span>
      </div>

      <div class="feature-tile tile-wine">
        <svg width="30" height="42" viewBox="0 0 30 42" aria-hidden="true">
          <path d="M16 2 C24 4 24 12 18 14 C18 8 16 6 16 2 Z" fill="#fff"/>
          <g fill="#fff">
            <circle cx="7" cy="18" r="3.5"/><circle cx="15" cy="18" r="3.5"/><circle cx="23" cy="18" r="3.5"/>
            <circle cx="11" cy="25" r="3.5"/><circle cx="19" cy="25" r="3.5"/>
            <circle cx="7" cy="25" r="0"/><circle cx="15" cy="32" r="3.5"/>
          </g>
        </svg>
        <span>Wineries<br>&amp; Vineyards</span>
      </div>
      <div class="photo photo-pour" role="img" aria-label="Red wine pouring from a bottle into two glasses"></div>

      <div class="photo photo-orchard" role="img" aria-label="Apple orchard with red apples, ladder and wooden barrels"></div>
      <div class="photo photo-industry" role="img" aria-label="Industrial workers in hard hats handling pipe at a plant"></div>

      <div class="photo photo-hay" role="img" aria-label="Round hay bales on a golden harvested field"></div>
      <div class="feature-tile tile-agri">
        <svg width="66" height="44" viewBox="0 0 66 44" aria-hidden="true">
          <path d="M16 4 C12 10 12 16 16 20 C20 16 20 10 16 4 Z M8 10 C8 16 12 20 16 20 C14 15 12 12 8 10 Z M24 10 C20 12 18 15 16 20 C20 20 24 16 24 10 Z" fill="#fff"/>
          <g fill="#fff">
            <circle cx="18" cy="30" r="8"/>
            <rect x="16" y="19" width="4" height="22"/><rect x="7" y="28" width="22" height="4"/>
            <circle cx="46" cy="26" r="11"/>
            <rect x="43" y="11" width="6" height="30"/><rect x="31" y="23" width="30" height="6"/>
            <rect x="43" y="11" width="6" height="30" transform="rotate(45 46 26)"/>
            <rect x="43" y="11" width="6" height="30" transform="rotate(-45 46 26)"/>
          </g>
          <circle cx="18" cy="30" r="3" fill="var(--blue)"/>
          <circle cx="46" cy="26" r="5" fill="var(--blue)"/>
        </svg>
        <span>Agriculture<br>&amp; Industries</span>
      </div>
    </section>

    <footer class="banner-footer">
      <div class="footer-title">Chamber of Commerce</div>
      <div class="footer-web">www.tourbrindley.ca</div>
    </footer>
  </main>
</body>
</html>
```